Business Card Design - Photographer

I am a landscape photographer and I require a business card design. 

I require two designs:
1)  a double sided business card
 and
b)  a single sided business card 

The single sided design can either be the same as the double sided (with just one side having all the information)....or it can be an entire new design. Its up to you.

My corporate colours are (CMYK):

Blue   69, 32, 0, 0
Grey  72,  64,  47,  31
Green  32,  2,  91,  0
Yellow   0, 19, 92, 0
Orange  0, 39, 75, 0

Colour space in final file should be in CMYK.

The details that need to be included on the card:

- Use the provided Logo
- Name: Wiktor Baranowski
- Email:   sales@vistalumeworks.com.au
- Website:    vistalumeworks.com.au
- Twitter:    twitter.com/vistalumeworks
- Facebook:   facebook.com/vistalumeworks
- Mobile  0417 539 662

Please use the attached template to design the logo to the specified size, including the marked bleed lines. I have also attached my logo in PNG (transparent background) and ai format for you to use.

The final file should be:
- Photoshop version with layers so I can edit the name/text etc. All non vector files should be high resolution at 1039 x 697 pixels at 300 dpi.

I also require a file as:
- Vector based PDF

Anyway questions please contact me.

Thank you

Industry/Entity Type

Landscape

Logo styles of interest
Pictorial/Combination Logo
Abstract Logo
Wordmark Logo
Lettermark Logo
Requirements
Must have
• The details that need to be included on the card:

- Use the provided Logo
- Name: Wiktor Baranowski
- Email: sales@vistalumeworks.com.au
- Website: vistalumeworks.com.au
- Twitter: twitter.com/vistalumeworks
- Facebook: facebook.com/vistalumeworks
- Mobile 0417 539 662

```html
<!DOCTYPE html>
<html lang="en">
<head>
<meta charset="utf-8">
<title>Vista Lume Works — Business Card</title>
<link rel="stylesheet" href="https://fonts.googleapis.com/css2?family=Cinzel:wght@400;600;700&display=swap">
<style>
  :root {
    --backdrop: #808185;
    --card: #ffffff;
    --ink: #3d4152;
    --blue: #3d8fcf;
    --white: #ffffff;
  }
  * { margin: 0; padding: 0; box-sizing: border-box; }
  html, body {
    width: 1200px; height: 736px; overflow: hidden;
    background: var(--backdrop);
  }
  .card {
    position: absolute; left: 136px; top: 101px;
    width: 937px; height: 535px;
    background: var(--card);
    border-radius: 28px;
    overflow: hidden;
    font-family: "Cinzel", "Times New Roman", serif;
    color: var(--ink);
  }
  .brand-mark {
    position: absolute; left: 408px; top: 47px;
    width: 156px; height: 156px;
  }
  .brand-name {
    position: absolute; left: 0; right: 0; top: 212px;
    text-align: center;
    font-size: 40px; font-weight: 400; letter-spacing: 1px;
    color: var(--ink);
  }
  .brand-rule {
    position: absolute; left: 279px; width: 416px; top: 262px;
    height: 2px; background: var(--ink);
  }
  .tagline {
    position: absolute; left: 0; right: 0; top: 273px;
    text-align: center;
    font-size: 15px; font-weight: 700; letter-spacing: 3.5px;
    color: var(--ink);
  }
  .contacts {
    position: absolute; left: 0; right: 0; top: 334px;
    text-align: center;
    font-size: 20px; line-height: 34px; letter-spacing: 0.6px;
  }
  .contacts .label { color: var(--blue); font-size: 21px; }
  .contacts .gap { display: inline-block; width: 14px; }
  .rule {
    position: absolute; left: 0; right: 0; top: 460px;
    height: 4px; background: var(--ink);
  }
  .web-band {
    position: absolute; left: 0; right: 0; top: 468px; bottom: 0;
    background: var(--blue);
    display: flex; align-items: center; justify-content: center;
    color: var(--white); font-weight: 600;
    font-size: 18px; letter-spacing: 0.5px;
  }
  .web-band .domain { font-size: 27px; }
</style>
</head>
<body>
  <div class="card">
    <svg class="brand-mark" viewBox="0 0 156 156" aria-hidden="true">
      <circle cx="78" cy="78" r="76" fill="var(--ink)"/>
    </svg>
    <div class="brand-name">VISTA LUME WORKS</div>
    <div class="brand-rule"></div>
    <div class="tagline">FINE ART PHOTOGRAPHY</div>
    <div class="contacts">
      <div><span class="label">E</span> : sales@vistalumeworks.com.au</div>
      <div><span class="label">T</span> : chirply.com/vistalumeworks<span class="gap"></span><span class="label">F</span> : meetfold.com/vistalumeworks</div>
      <div><span class="label">M</span> : 0417 539 662</div>
    </div>
    <div class="rule"></div>
    <div class="web-band">www.<span class="domain">VISTALUMEWORKS</span>.com.au</div>
  </div>
</body>
</html>
```